Re-design and craft the perfect CV platform

We are building a CV-based platform designed to connect employees and employers, with a strong focus on individual users. As we're just starting out, we're looking to have our platform and logo redesigned to better reflect our vision
https://app.zelvorhire.com/
Colors like in the logo attached
#87C032 #6A6E71 #618930 - also you can add more colors if you like.
https://app.zelvorhire.com/dashboard - This page would be nice if you plan it, like personal Bio dashboard. Attached picture (Dashboard wanted) one idea from how we would like to be, but we are open for new professional ideas/solutions.
https://app.zelvorhire.com/posts - On this page we want to be showed the jobs posted. Attached one picture about our idea (jobs page wanted)
https://app.zelvorhire.com/profile - design something nice.
Only Photoshop, Illustrator or Figma
Other pictures from the app attached (as looking right now)

Target Market(s)

Job seekers, HR, Recruiters

Industry/Entity Type

HR Tech

Number of Pages Required

5+ page

Colors
00AB8E
00BBA5
67D7C9
C6EFE9
E9F9F6

```html
<!DOCTYPE html>
<html lang="en">
<head>
<meta charset="utf-8">
<title>Zelvor Hire – Set up your profile</title>
<link href="https://fonts.googleapis.com/css2?family=Poppins:wght@400;500;600;700&display=swap" rel="stylesheet">
<style>
:root{
  --green:#87c032;
  --green-dark:#618930;
  --grey:#6a6e71;
  --text:#4a4d50;
  --muted:#8a8d90;
  --field:#f0f0f1;
  --band:#ebebed;
  --page:#f4f4f5;
  --white:#ffffff;
  --line:#d6d7d9;
}
*{box-sizing:border-box;margin:0;padding:0}
html,body{width:1200px;height:712px;overflow:hidden}
body{font-family:'Poppins',sans-serif;background:var(--page);position:relative;color:var(--text)}
.top-band{position:absolute;left:0;top:0;width:1200px;height:142px;background:var(--band)}
.brand{position:absolute;left:37px;top:28px;display:flex;align-items:center;gap:7px}
.brand-dot{width:14px;height:14px;border-radius:50%;background:var(--green)}
.brand-name{font-size:17px;font-weight:600;color:var(--green);letter-spacing:.3px}
.header-divider{position:absolute;left:152px;top:19px;width:1px;height:52px;background:#d0d1d3}
.main-nav a{position:absolute;top:40px;font-size:10.5px;font-weight:500;color:var(--text);text-decoration:none;letter-spacing:.2px}
.main-nav a.active{color:var(--green);font-weight:600;padding-bottom:4px;border-bottom:1.5px solid var(--green)}
.pill{position:absolute;top:27px;width:84px;height:33px;border:1px solid var(--grey);border-radius:17px;display:flex;align-items:center;justify-content:center;gap:6px;font-size:11.5px;font-weight:500;color:var(--text)}
.icon-btn{position:absolute;top:35px}
.card{position:absolute;left:39px;top:94px;width:1123px;height:576px;background:var(--white);border-radius:12px;box-shadow:0 4px 20px rgba(0,0,0,.04)}
.back-btn{position:absolute;left:88px;top:125px;width:93px;height:36px;border-radius:18px;background:var(--field);display:flex;align-items:center;justify-content:center;gap:6px;font-size:12px;font-weight:500;color:var(--grey)}
.page-title{position:absolute;left:0;width:1200px;top:122px;text-align:center;font-size:31px;font-weight:600;color:var(--grey)}
.page-sub{position:absolute;left:0;width:1200px;top:171px;text-align:center;font-size:13.5px;color:var(--muted)}
.continue-btn{position:absolute;left:995px;top:125px;width:115px;height:37px;border-radius:19px;background:var(--green);color:var(--white);display:flex;align-items:center;justify-content:center;gap:6px;font-size:12px;font-weight:600}
.steps-line{position:absolute;left:204px;top:249px;width:792px;border-top:1px dashed var(--line)}
.step{position:absolute;top:234px;width:120px;margin-left:-60px;text-align:center}
.step-dot{width:32px;height:32px;margin:0 auto;border-radius:50%;background:#ececee;display:flex;align-items:center;justify-content:center}
.step.active .step-dot{background:var(--green)}
.step-num{margin-top:8px;font-size:12px;font-weight:500;color:var(--grey);line-height:14px}
.step-label{font-size:9.5px;color:var(--text);line-height:13px}
.step.active .step-num,.step.active .step-label{color:var(--green);font-weight:600}
.avatar-ring{position:absolute;left:199.5px;top:379.5px;width:192px;height:192px;border-radius:50%;border:1px solid var(--green)}
.avatar{position:absolute;left:209.5px;top:389.5px;width:172px;height:172px;border-radius:50%;background:radial-gradient(circle at 50% 40%,#b9a08a 0%,#9f8a78 40%,#b8babb 70%,#c4c6c8 100%)}
.upload{position:absolute;left:205px;top:587px;display:flex;align-items:center;gap:8px}
.upload span{font-size:14.5px;font-weight:600;color:var(--grey);text-decoration:underline;text-underline-offset:3px;text-decoration-thickness:1px}
.field{position:absolute;width:170px}
.field label{display:block;font-size:10px;font-weight:600;color:var(--text);height:12px;line-height:12px}
.field label i{color:var(--green);font-style:normal}
.field .input{margin-top:12px;height:36px;border-radius:18px;background:var(--field);padding:0 20px;display:flex;align-items:center;justify-content:space-between;font-size:11px;color:var(--grey)}
.save-btn{position:absolute;left:440px;top:592px;width:170px;height:37px;border-radius:19px;background:var(--green);color:var(--white);display:flex;align-items:center;justify-content:center;gap:6px;font-size:13px;font-weight:700;letter-spacing:.3px}
</style>
</head>
<body>
<div class="top-band"></div>

<header>
  <div class="brand"><span class="brand-dot"></span><span class="brand-name">Zelvor Hire</span></div>
  <div class="header-divider"></div>
  <nav class="main-nav">
    <a href="https://app.zelvorhire.com/dashboard" style="left:175px">DASHBOARD</a>
    <a href="https://app.zelvorhire.com/profile" class="active" style="left:273px">PROFILE</a>
    <a href="https://app.zelvorhire.com/posts" style="left:349px">JOB POSTS</a>
  </nav>
  <div class="pill" style="left:908px">
    <svg width="12" height="10" viewBox="0 0 12 10"><rect x="0" y="2" width="12" height="8" rx="1.5" fill="#87c032"/><rect x="4" y="0" width="4" height="3" rx="1" fill="none" stroke="#87c032" stroke-width="1.2"/></svg>Jobs</div>
  <div class="pill" style="left:1001px">
    <svg width="10" height="12" viewBox="0 0 10 12"><path d="M0 1.5A1.5 1.5 0 0 1 1.5 0H6l4 4v6.5A1.5 1.5 0 0 1 8.5 12h-7A1.5 1.5 0 0 1 0 10.5z" fill="#87c032"/><rect x="2.5" y="6" width="4" height="1" fill="#fff"/><rect x="2.5" y="8" width="4" height="1" fill="#fff"/></svg>CV</div>
  <svg class="icon-btn" style="left:1108px" width="18" height="19" viewBox="0 0 18 19"><path d="M9 1a5 5 0 0 1 5 5v4l2 3H2l2-3V6a5 5 0 0 1 5-5z" fill="#6a6e71"/><circle cx="9" cy="16" r="2" fill="#6a6e71"/><circle cx="14" cy="3" r="3" fill="#e53935"/></svg>
  <svg class="icon-btn" style="left:1147px" width="18" height="18" viewBox="0 0 18 18"><circle cx="7" cy="5" r="4" fill="#6a6e71"/><path d="M0 17c0-4 3-6 7-6s5 1 6 2l-3 4z" fill="#6a6e71"/><path d="M11 16l5-5 1.5 1.5-5 5H11z" fill="#6a6e71"/></svg>
</header>

<main class="card"></main>

<div class="back-btn"><svg width="14" height="12" viewBox="0 0 14 12"><path d="M13 6H1M6 1L1 6l5 5" fill="none" stroke="#6a6e71" stroke-width="1.5" stroke-linecap="round" stroke-linejoin="round"/></svg>Back</div>
<h1 class="page-title">Set up your profile</h1>
<p class="page-sub">Build your CV in six easy steps</p>
<div class="continue-btn">Continue<svg width="14" height="12" viewBox="0 0 14 12"><path d="M1 6h12M8 1l5 5-5 5" fill="none" stroke="#fff" stroke-width="1.5" stroke-linecap="round" stroke-linejoin="round"/></svg></div>

<div class="steps-line"></div>
<div class="step active" style="left:204px"><div class="step-dot"><svg width="11" height="13" viewBox="0 0 10 12"><path d="M0 1.5A1.5 1.5 0 0 1 1.5 0H6l4 4v6.5A1.5 1.5 0 0 1 8.5 12h-7A1.5 1.5 0 0 1 0 10.5z" fill="#fff"/><rect x="2.5" y="7" width="4" height="1" fill="#87c032"/></svg></div><div class="step-num">1</div><div class="step-label">Personal Details</div></div>
<div class="step" style="left:336px"><div class="step-dot"><svg width="12" height="12" viewBox="0 0 12 12"><circle cx="6" cy="6" r="6" fill="#6a6e71"/><rect x="5.3" y="5" width="1.4" height="4" fill="#fff"/><circle cx="6" cy="3.3" r=".8" fill="#fff"/></svg></div><div class="step-num">2</div><div class="step-label">Bio</div></div>
<div class="step" style="left:468px"><div class="step-dot"><svg width="13" height="11" viewBox="0 0 12 10"><rect x="0" y="2" width="12" height="8" rx="1.5" fill="#6a6e71"/><rect x="4" y="0" width="4" height="3" rx="1" fill="none" stroke="#6a6e71" stroke-width="1.2"/></svg></div><div class="step-num">3</div><div class="step-label">Work Experience</div></div>
<div class="step" style="left:600px"><div class="step-dot"><svg width="14" height="11" viewBox="0 0 14 11"><path d="M7 0l7 3.5L7 7 0 3.5z" fill="#6a6e71"/><path d="M3 5.5v3c0 1 2 2 4 2s4-1 4-2v-3L7 7.5z" fill="#6a6e71"/></svg></div><div class="step-num">4</div><div class="step-label">Education</div></div>
<div class="step" style="left:732px"><div class="step-dot"><svg width="14" height="14" viewBox="0 0 14 14"><circle cx="7" cy="7" r="3.2" fill="#6a6e71"/><rect x="5.5" y="10" width="3" height="2.5" fill="#6a6e71"/><path d="M7 0v2M1 3l1.4 1.2M13 3l-1.4 1.2M0 8h2M12 8h2" stroke="#6a6e71" stroke-width="1.2"/></svg></div><div class="step-num">5</div><div class="step-label">Skills</div></div>
<div class="step" style="left:864px"><div class="step-dot"><svg width="13" height="12" viewBox="0 0 13 12"><path d="M0 2h13M0 6h13M0 10h13" stroke="#6a6e71" stroke-width="1.3"/><rect x="3" y="0.5" width="2" height="3" fill="#6a6e71"/><rect x="8" y="4.5" width="2" height="3" fill="#6a6e71"/><rect x="4" y="8.5" width="2" height="3" fill="#6a6e71"/></svg></div><div class="step-num">6</div><div class="step-label">Preferences</div></div>
<div class="step" style="left:996px"><div class="step-dot"><svg width="12" height="12" viewBox="0 0 12 12"><circle cx="6" cy="6" r="6" fill="#6a6e71"/><path d="M3.3 6.2l1.8 1.8 3.6-3.6" fill="none" stroke="#fff" stroke-width="1.4"/></svg></div><div class="step-num">7</div><div class="step-label">Done</div></div>

<div class="avatar-ring"></div>
<div class="avatar" role="img" aria-label="Profile photo of the user"></div>
<div class="upload">
  <svg width="16" height="18" viewBox="0 0 16 18"><path d="M8 12V2M3.5 6.5L8 2l4.5 4.5" fill="none" stroke="#87c032" stroke-width="2" stroke-linecap="round" stroke-linejoin="round"/><path d="M1 12v4.5h14V12" fill="none" stroke="#87c032" stroke-width="2" stroke-linecap="round" stroke-linejoin="round"/></svg>
  <span>Upload Profile Picture</span>
</div>

<div class="field" style="left:440px;top:360px"><label>Name<i>*</i></label><div class="input">Dana Weller</div></div>
<div class="field" style="left:625px;top:360px"><label>Email Address<i>*</i></label><div class="input">hello@danaweller.net</div></div>
<div class="field" style="left:809px;top:360px"><label>Phone Number<i>*</i></label><div class="input">+08 555 210 4471</div></div>

<div class="field" style="left:440px;top:435px"><label>Date of Birth<i>*</i></label><div class="input">1988-12-01<svg width="14" height="14" viewBox="0 0 14 14"><rect x="0.6" y="1.6" width="12.8" height="11.8" rx="1.5" fill="none" stroke="#87c032" stroke-width="1.1"/><path d="M0.6 4.5h12.8M4 0v3M10 0v3" stroke="#87c032" stroke-width="1.1"/><g fill="#87c032"><rect x="3" y="6.5" width="1.5" height="1.3"/><rect x="6.2" y="6.5" width="1.5" height="1.3"/><rect x="9.4" y="6.5" width="1.5" height="1.3"/><rect x="3" y="9.4" width="1.5" height="1.3"/><rect x="6.2" y="9.4" width="1.5" height="1.3"/><rect x="9.4" y="9.4" width="1.5" height="1.3"/></g></svg></div></div>
<div class="field" style="left:625px;top:435px"><label>Address<i>*</i></label><div class="input"></div></div>
<div class="field" style="left:809px;top:435px"><label>City<i>*</i></label><div class="input"></div></div>

<div class="field" style="left:440px;top:510px"><label>State<i>*</i></label><div class="input"></div></div>
<div class="field" style="left:625px;top:510px"><label>Post Code<i>*</i></label><div class="input"></div></div>
<div class="field" style="left:809px;top:510px"><label>Country<i>*</i></label><div class="input"></div></div>

<div class="save-btn"><svg width="14" height="14" viewBox="0 0 14 14"><path d="M0 1.5A1.5 1.5 0 0 1 1.5 0H11l3 3v9.5a1.5 1.5 0 0 1-1.5 1.5h-11A1.5 1.5 0 0 1 0 12.5z" fill="#fff"/><rect x="3" y="1.5" width="6" height="3.5" fill="#87c032"/><circle cx="7" cy="9.5" r="2" fill="#87c032"/></svg>SAVE</div>
</body>
</html>
```